Sales Proposal Template Design

I sell Internet Marketing services; including search engine optimization, search engine marketing, social media, websites, mobile websites, email and video.

I produce a proposal for each prospective client. Some include SEO and PPC. Other include more services or less services. The purpose of this project is to create a template in MS Word or Power Point. I will add standard content for each product with different pricing for different projects.

I want one page for each product or service I will be presenting the the proposal. I can then use just one page or multiple pages to build the full proposal.

Once I am finished I will convert the single sheets into a PDF document to print or send to the client via email.

I am part of a the This is a KVO Franchise http://www.kvoglobe-example.com/ you can see the corporate colors and design on this website.

I would like both a vertical and horizontal orientation template.

Target Market(s)

Prospects and buyers that request information and pricing.

Industry/Entity Type

Internet

Requirements
Must have
• Must have the KVO logo and be consistent with their colors and design feel.

I need a lot of open space for content copy.

The template needs to be in MS Word or Power Point.
Nice to have
• A front cover design that matches the inside page template would be nice to have.

```html
<!DOCTYPE html>
<html lang="en">
<head>
<meta charset="utf-8">
<title>KVO – Proposal Template, Follow-up Page</title>
<link rel="stylesheet" href="https://fonts.googleapis.com/css2?family=Source+Sans+3:wght@300;600&display=swap">
<style>
  :root {
    --canvas: #ffffff;
    --paper: #ffffff;
    --shadow: rgba(0, 0, 0, 0.35);
    --navy: #1d2f4f;
    --aqua-deep: #a9dde9;
    --aqua: #c6e9ef;
    --aqua-soft: #e3f4f5;
    --caption: #3f3f3f;
  }
  * { margin: 0; padding: 0; box-sizing: border-box; }
  html, body {
    width: 1200px;
    height: 900px;
    overflow: hidden;
    background: var(--canvas);
  }
  .canvas {
    position: relative;
    width: 1200px;
    height: 900px;
  }
  .page {
    position: absolute;
    left: 302px;
    top: 29px;
    width: 595px;
    height: 840px;
    background: var(--paper);
    box-shadow: 8px 8px 14px var(--shadow);
    overflow: hidden;
  }
  .page__art {
    position: absolute;
    left: 0;
    top: 0;
    width: 165px;
    height: 100%;
    background:
      linear-gradient(to right, rgba(255,255,255,0) 50%, var(--paper) 100%),
      linear-gradient(to bottom, var(--aqua-soft) 0%, var(--aqua) 30%, var(--aqua-deep) 55%, var(--aqua) 80%, var(--aqua-soft) 100%);
  }
  .brand {
    position: absolute;
    left: 34px;
    top: 766px;
    display: flex;
    align-items: center;
    gap: 14px;
    font-family: "Source Sans 3", sans-serif;
    font-weight: 600;
    color: var(--navy);
  }
  .brand__name {
    font-size: 38px;
    line-height: 1;
    letter-spacing: 1px;
  }
  .brand__tagline {
    font-size: 11px;
    line-height: 1.2;
  }
  .brand__tagline span { display: block; }
  .caption {
    position: absolute;
    left: 914px;
    top: 850px;
    font-family: "Source Sans 3", sans-serif;
    font-weight: 300;
    font-size: 16px;
    letter-spacing: 0.2px;
    color: var(--caption);
    white-space: nowrap;
  }
</style>
</head>
<body>
  <div class="canvas">
    <div class="page">
      <div class="page__art" role="img" aria-label="Abstract composition of translucent aqua and pale green rectangles receding in perspective along the left edge"></div>
      <div class="brand">
        <span class="brand__name">KVO</span>
        <span class="brand__tagline"><span>clear paths</span><span>online</span></span>
      </div>
    </div>
    <p class="caption">WORD Template - follow up&nbsp; page</p>
  </div>
</body>
</html>
```